Hardcore nerd needs to stand out in a sea of dull Defence business cards

Wombarra Devices is a new Australian consulting engineering company that turns research and theory into practical systems. No evangelistic fluff, just mathematics and physics into electronic and optical circuits for consumer products, scientific research or Defence applications.

We already have a recognised logo (provided) which is often dark blue/black on a light background but we're open to other combinations. (Us engineers tend to have limited aesthetic imagination :)

Some of our recent products have included:
* Instrumentation for electrical testing,
* Radar jammers,
* GPS antenna design,
* Satellite tracking systems,
* High power lasers

We're open to both single and double-sided designs - happy to be convinced either way.

P.S. Another group is working on the web page, so - alas - our web site is currently of no use for images/ideas...

Target Market(s)

Engineering managers,
Scientists

Contact Information for Business Card

Dr Colin Harte
R&D Engineer

colin@wombarradevices.com.au
0427 563 710

PO Box XXX (to be confirmed)
Kelsby ACT 2917
Australia

Font styles to use
Serif
Sans Serif

Colors

Designer to choose colors to be used in the design.

Requirements
Must have
• My contact details!
• I've had many (great) "bold and plain" designs submitted already, so feel free to be artistically creative :)
• Happy to take advice re fonts/colours/printability etc.
Nice to have
• I'm not sure if "lists" are more at home on a CV than a business card, but representative services include:
• Applied electromagnetics
• RF and high speed electronics
• Signal and image processing
• Electro-optical and laser systems
• Concept-to-prototype design services
• If you're considering double sided cards, then often measuring/alignment grids/rulers feature on the back of similar cards.
• e.g. https://www.veltranoptics.example/newgrouppage9.cfm?objectgroup_id=4183
• https://www.veltranoptics.example/newgrouppage9.cfm?objectgroup_ID=4185
• ..or even a "Smith chart" (google will return lots)
• Generic images to represent a capability might work - googling images associated with keyword for each of these areas might help:
• - "passive radar", "phased array", "fdtd", "vircator"
• RF and high speed electronic design
• - "smith chart", "microstrip circuits", "dimensioned drawing", "electronic schematic"
• - "dft", "iir filter"
• - "optical cavity". "laser energy level diagram"
• Background/watermarked images outlines/wireframes/schematics would probably look OK.
Should not have
• If a list of projects/services is provided, it is important not to make the client feel that this is "all" the company can do. Engineering design is a creative discipline (like graphics :)
• Please, no stock "military" snaps like planes, missiles, etc!

```html
<!DOCTYPE html>
<html lang="en">
<head>
<meta charset="utf-8">
<title>Wombarra Devices – Business Card</title>
<link href="https://fonts.googleapis.com/css2?family=Lato:wght@400;700;900&display=swap" rel="stylesheet">
<style>
  :root {
    --navy: #2b2f7a;
    --navy-deep: #262a6e;
    --ink: #3a3a44;
    --paper: #ffffff;
    --backdrop: #e4e5ea;
    --mist: #eef0f5;
  }
  * { box-sizing: border-box; margin: 0; padding: 0; }
  html, body {
    width: 1200px; height: 900px; overflow: hidden;
    background: var(--backdrop);
    font-family: "Lato", sans-serif;
  }
  .stage {
    position: relative; width: 1200px; height: 900px;
  }
  .card {
    position: absolute; left: 337px;
    width: 526px; height: 300px;
    border-radius: 22px; overflow: hidden;
    background: var(--paper);
    box-shadow: 0 6px 24px rgba(30, 32, 70, 0.18);
  }
  .card--front { top: 110px; }
  .card--back { top: 490px; }

  /* Front */
  .brand {
    position: absolute; left: 34px; top: 30px;
    display: flex; align-items: center; gap: 12px;
  }
  .brand__dot {
    width: 40px; height: 40px; border-radius: 50%;
    background: var(--navy);
  }
  .brand__name {
    color: var(--navy); font-weight: 900;
    font-size: 22px; line-height: 1; letter-spacing: 0.5px;
    text-transform: uppercase;
  }
  .contact {
    position: absolute; left: 38px; top: 100px;
    color: var(--ink); font-size: 13px; line-height: 20px;
    list-style: none;
  }
  .contact__line { display: flex; align-items: center; gap: 8px; }
  .contact__line--plain { padding-left: 22px; }
  .contact__icon { width: 14px; height: 14px; flex: none; }
  .person {
    position: absolute; right: 48px; bottom: 40px; text-align: right;
  }
  .person__name {
    color: var(--navy); font-weight: 900; font-size: 27px; line-height: 1.1;
  }
  .person__role {
    color: var(--ink); font-size: 14px; margin-top: 4px;
  }
  .edge-tab {
    position: absolute; right: 0; bottom: 22px;
    width: 22px; height: 52px; background: var(--navy);
  }

  /* Back */
  .back-field {
    position: absolute; left: 0; top: 0; bottom: 0; width: 384px;
    background: linear-gradient(135deg, var(--navy) 0%, var(--navy-deep) 100%);
  }
  .products {
    position: absolute; left: 36px; top: 36px; color: var(--paper);
  }
  .products__title {
    font-weight: 900; font-size: 22px; letter-spacing: 0.5px; margin-bottom: 12px;
  }
  .products__list { list-style: none; font-size: 15px; line-height: 26px; }
  .products__item { display: flex; align-items: center; gap: 10px; }
  .products__bullet {
    width: 9px; height: 9px; border-radius: 50%;
    background: var(--paper); flex: none;
  }
  .back-brand {
    position: absolute; left: 384px; right: 0; top: 0; bottom: 0;
    display: flex; flex-direction: column; align-items: center; justify-content: center; gap: 12px;
  }
  .back-brand__dot {
    width: 46px; height: 46px; border-radius: 50%; background: var(--navy);
  }
  .back-brand__name {
    color: var(--navy); font-weight: 900; font-size: 19px; line-height: 1.15;
    text-transform: uppercase; text-align: center; letter-spacing: 0.5px;
  }
</style>
</head>
<body>
<main class="stage">

  <section class="card card--front" aria-label="Card front">
    <div class="brand">
      <span class="brand__dot"></span>
      <span class="brand__name">Wombarra Devices</span>
    </div>

    <ul class="contact">
      <li class="contact__line contact__line--plain">PO Box XXX</li>
      <li class="contact__line contact__line--plain">Kelsby ACT 2917, Australia</li>
      <li class="contact__line">
        <svg class="contact__icon" viewBox="0 0 16 16"><path d="M4 1.5l2.5 3-1.5 1.7a9 9 0 0 0 4.8 4.8l1.7-1.5 3 2.5-1.6 2.3C7.5 14 2 8.5 1.7 3.1z" fill="#2b2f7a"/></svg>
        0427 563 710
      </li>
      <li class="contact__line">
        <svg class="contact__icon" viewBox="0 0 16 16"><rect x="1" y="3" width="14" height="10" rx="1.5" fill="#2b2f7a"/><path d="M1.5 4l6.5 5 6.5-5" fill="none" stroke="#fff" stroke-width="1.3"/></svg>
        colin@wombarradevices.com.au
      </li>
      <li class="contact__line">
        <svg class="contact__icon" viewBox="0 0 16 16"><circle cx="8" cy="8" r="6.5" fill="none" stroke="#2b2f7a" stroke-width="1.5"/><path d="M1.5 8h13M8 1.5c-3 3.5-3 9.5 0 13M8 1.5c3 3.5 3 9.5 0 13" fill="none" stroke="#2b2f7a" stroke-width="1.2"/></svg>
        www.wombarradevices.com.au
      </li>
    </ul>

    <div class="person">
      <p class="person__name">Dr Colin Harte</p>
      <p class="person__role">R&amp;D Engineer</p>
    </div>
    <span class="edge-tab"></span>
  </section>

  <section class="card card--back" aria-label="Card back">
    <div class="back-field" role="img" aria-label="Navy panel with a faint repeating tonal pattern"></div>
    <div class="products">
      <h2 class="products__title">PRODUCTS:</h2>
      <ul class="products__list">
        <li class="products__item"><span class="products__bullet"></span>Instrumentation for electrical testing</li>
        <li class="products__item"><span class="products__bullet"></span>Radar jammers</li>
        <li class="products__item"><span class="products__bullet"></span>GPS antenna design</li>
        <li class="products__item"><span class="products__bullet"></span>Satellite tracking systems</li>
        <li class="products__item"><span class="products__bullet"></span>High power lasers</li>
      </ul>
    </div>
    <div class="back-brand">
      <span class="back-brand__dot"></span>
      <span class="back-brand__name">Wombarra<br>Devices</span>
    </div>
  </section>

</main>
</body>
</html>
```